Stationery Design Project

We need a stationery design for our Norwegian trucking company. We have existed for about 15 years and our 12 drivers uses relatively new vehicles to transport goods around in northern Norway. Long distance routes with fresh fish og food transport is our main operations.

We have already made alogo that's printed on our trucks. The logo and a picture of our trucks is attached. I think the logo i crappy, but since its already in use, changing it is not an option in this round. Still using a better colour scheme in the overall stationery and more interesting fonts is possible (altso in the logo).

Company details:
Name: Kjelvraket AS
Organisation nr 873 615 309
Post adress: 8642 Raudvik

I like minimalism and simplicity. I am avalibly for questions in normal GMT working hours either here or on mail: ivar@fjordlast.no

Reason: Hi. Im extending the deadline because I needed some time to find a vector file of our logo. Sorry for the inconvenience

Hi, and thanks for all your interest in the project. Some updates:

-          I have decided to commit to using one of the designs. Some designer will get the payment.

-          I have extended the deadline with 24 hours since I needed some time to find our firms vector logo (a slow Swedish man was holding me up)

-          We will not choose a design before the deadline. No need to rush.

-          We have received a lot of great design and think there is a need to specified the product we want to make:

o   Business Card for all our employers. I just need the design and will duplicate with the correct numbers and name myself. The information on should be: Logo, employer’s name, Phone number, email, website, Postal number and address. Use this as a template: logo, Leif Brattvoll, 47382066, Leif@fjordlast.no,, fjordlast.no, 8642 Raudvik. The order and placement of the information is your creative decision.

o   Stickers to put on the goods we travel. On the sticker the should be the following information: Logo, phone number, Tekst and link: Fraktæ av Kjelvraket. Ke du syns? Fjordlast.no/tilbakemelding (this means: Handled by Kjelvraket. What do you think Fjordlast.no/feedback -à the link will be a feedback form). The placement the information and size is your creative decision with some stings: we have been thinking of using Drukko for printing and see that a size about 6x6 cm, 8x5 or something like that. (with 3000 copies our budget is 200 punds). Any suggestions of other suppliers are welcome. Drukko price calculator http://www.drukkolabelhouse.co.uk/digital-litho-printing/printing-labels-tags/stickers/

o   Letterhead with logo, address, phone number and organizational number.

o   Envelopes with logo,address, phone number and organizational number.

Have a nice day.

 

 

• Using the blue colour in the logo and using a similar graphic approch.

```html
<!DOCTYPE html>
<html lang="en">
<head>
<meta charset="utf-8">
<title>Kjelvraket business cards</title>
<link rel="stylesheet" href="https://fonts.googleapis.com/css2?family=PT+Sans:wght@400;700&display=swap">
<style>
  :root {
    --backdrop: #2a2a2c;
    --card-white: #ffffff;
    --card-dark: #252525;
    --brand-blue: #1f5db4;
    --brand-blue-deep: #0f3f91;
    --brand-blue-light: #3f86d6;
    --ink: #333333;
    --ink-soft: #555555;
    --ink-light: #b8b8b8;
  }
  * { margin: 0; padding: 0; box-sizing: border-box; }
  html, body { width: 1200px; height: 266px; overflow: hidden; background: var(--backdrop); }
  .canvas { position: relative; width: 1200px; height: 266px; font-family: "PT Sans", sans-serif; }
  .card {
    position: absolute; top: 27px; width: 361px; height: 209px;
    border-radius: 14px; overflow: hidden;
  }
  .card--front { left: 13px; background: var(--card-white); }
  .card--back-light { left: 411px; background: var(--card-white); }
  .card--back-dark { left: 815px; background: var(--card-dark); }
  .card__swoosh { position: absolute; inset: 0; }
  .wordmark {
    position: absolute; font-weight: 700; color: var(--brand-blue);
    letter-spacing: 0.5px; white-space: nowrap; line-height: 1;
  }
  .card--front .wordmark { left: 26px; top: 34px; font-size: 34px; }
  .card--back-light .wordmark,
  .card--back-dark .wordmark { left: 0; right: 0; top: 84px; text-align: center; font-size: 36px; }
  .card--back-dark .wordmark { color: var(--brand-blue-light); }
  .contact {
    position: absolute; left: 26px; top: 96px;
    font-size: 8.5px; line-height: 16px; color: var(--ink); white-space: nowrap;
  }
  .contact__name { font-size: 11px; line-height: 18px; color: var(--brand-blue); }
  .web {
    position: absolute; left: 0; right: 0; bottom: 20px; text-align: center;
    font-size: 8px; line-height: 10px; letter-spacing: 3.2px; color: var(--ink-soft);
  }
  .card--back-dark .web { color: var(--ink-light); }
</style>
</head>
<body>
<main class="canvas">
  <section class="card card--front">
    <svg class="card__swoosh" viewBox="0 0 361 209" preserveAspectRatio="none" aria-hidden="true">
      <path d="M318 0 C300 80 260 160 170 209 L361 209 L361 0 Z" fill="var(--brand-blue-deep)"/>
      <path d="M330 0 C320 70 290 150 215 209 L361 209 L361 0 Z" fill="var(--brand-blue)"/>
      <path d="M306 0 C296 70 250 150 175 209 L196 209 C270 150 312 80 318 0 Z" fill="var(--brand-blue-light)" opacity="0.85"/>
    </svg>
    <div class="wordmark">Kjelvraket</div>
    <div class="contact">
      <p class="contact__name">Leif Brattvoll</p>
      <p>phone : 47382066</p>
      <p>email : Leif@fjordlast.no</p>
      <p>web : www.fjordlast.no</p>
      <p>8642 Raudvik.</p>
      <p>Organisation nr 873 615 309</p>
    </div>
  </section>
  <section class="card card--back-light">
    <div class="wordmark">Kjelvraket</div>
    <p class="web">www.fjordlast.no</p>
  </section>
  <section class="card card--back-dark">
    <div class="wordmark">Kjelvraket</div>
    <p class="web">www.fjordlast.no</p>
  </section>
</main>
</body>
</html>
```